Personal Training Business at home (Fern Vitality & Health)

My business name will be Fern Vitality & Health and will be training people with special needs (Asthma, Diabetes, Obesity, Rehab, Sports Performance) for all ages. It will be set indoor and outdoor for all types of weather conditions. I,m also doing Pilates group classes as well in a Japanese garden setting.I will be working alone so the groups will be small and the client has a high quality of service. I just need something very basic to start with then as the business expands I can edit it to it,s growth.

Target Market(s)

Target special population persons with dysfunctions injuries, metabolic/cardio-respiratory conditions, sports performance and more also healthy food choices.

Industry/Entity Type

Business

Number of Pages Required

3 page

Font styles to use
Serif

Colors
f78f20
ffffff
474747
cbcbcb
abd036

Requirements
Must have
• The website must have accessibility for change, to be able to link on other networks like my own video player videos. A basic lay out so I can fill in the pages and ad more as I expand the business. The logo to have the A for Fern to be an image of a man shaped as the letter A with his arms extended out/up. Private Facility and must ring for appointment to enter premises.
Nice to have
• The Image I want to have in my studio is for people to be serious about training & health choices. I want them to be able to train in a comfortable environment and free of air conditioned concrete rooms with machines. My home is converted to a Organic feature and outdoor/indoor training facility that my clients & I can share the natural freedom of training in the elements. My client have special needs and need extra care, they are people with injuries, metabolic/cardio-respiratory condition, asthmatics & more they need to be screened and tested for the condition that they suffer from and together with there allied professional we work together to treat them with the up most care for maximum results. This is what I want to target I long term client with real Goals on there mind and not some pipe dream.
Should not have
• Not to be portray as a Gym with machines and clients that only care about image.

```html
<!DOCTYPE html>
<html lang="en">
<head>
<meta charset="utf-8">
<title>Fern Vitality &amp; Health</title>
<link href="https://fonts.googleapis.com/css2?family=Open+Sans:wght@300;400;600;700&display=swap" rel="stylesheet">
<style>
:root{
  --orange:#f78f20;
  --green:#abd036;
  --dark:#474747;
  --darker:#3b3b3b;
  --grey:#cbcbcb;
  --text:#555555;
  --white:#ffffff;
}
*{box-sizing:border-box;margin:0;padding:0}
html,body{width:705px;height:1200px;overflow:hidden;background:var(--white)}
body{position:relative;font-family:"Open Sans",Arial,sans-serif;color:var(--text)}
.abs{position:absolute}
.topbar{left:0;top:0;width:705px;height:18px;background:var(--green);color:var(--white);font-size:6.5px}
.topbar .social{left:78px;top:5px;display:flex;gap:5px}
.topbar .social span{width:7px;height:7px;border-radius:50%;background:var(--white);opacity:.9}
.topbar .contact{right:78px;top:4px;display:flex;gap:12px}
.header{left:0;top:18px;width:705px;height:54px;background:var(--white);border-bottom:1px solid #e6e6e6}
.logo{left:78px;top:16px;font-size:17px;font-weight:700;color:var(--orange);letter-spacing:.2px}
.nav{top:24px;left:275px;display:flex;gap:0;font-size:7px;text-transform:uppercase;color:#333}
.nav a{color:inherit;text-decoration:none;margin-right:31px}
.nav a.active{color:var(--green)}
.hero{left:0;top:72px;width:705px;height:315px;background:linear-gradient(100deg,#d8d2cb 0%,#c9a79f 25%,#b58a86 45%,#c7bcae 70%,#d9cdb8 100%)}
.hero svg{position:absolute;left:0;top:0}
.hero-title{right:78px;top:113px;font-size:19.5px;font-weight:300;color:var(--white);text-align:right}
.hero-text{right:78px;top:145px;width:290px;font-size:7px;line-height:12px;color:var(--white);text-align:right}
.about-photo{left:78px;top:410px;width:136px;height:136px;border-radius:50%;border:3px solid var(--white);box-shadow:0 0 4px rgba(0,0,0,.35);background:radial-gradient(circle at 50% 45%,#c9a08a 0 30%,#6f8f5a 55%,#3f6a8e 100%)}
.section-title{font-size:12.5px;font-weight:400;color:#333;text-transform:uppercase}
.about-title{left:235px;top:419px}
.about-text{left:235px;top:444px;width:389px;font-size:6.8px;line-height:12.2px;text-align:justify}
.btn{left:233px;top:517px;width:55px;height:20px;background:var(--green);color:var(--white);font-size:6.5px;line-height:20px;text-align:center;border-radius:2px}
.rule{left:78px;width:549px;height:1px;background:#ececec}
.services-title{left:78px;top:590px}
.arrows{left:612px;top:592px}
.card{top:622px;width:129px;height:177px;border-radius:2px;overflow:hidden;color:var(--white)}
.card.orange{background:var(--orange)}
.card.green{background:var(--green)}
.card .pic{height:93px}
.card h3{font-size:9px;font-weight:600;margin:10px 9px 6px}
.card p{font-size:6.3px;line-height:10.5px;margin:0 9px;opacity:.9}
.card .more{font-size:6.3px;margin:6px 9px 0}
.why-title{left:78px;top:843px}
.why-photo{left:78px;top:872px;width:121px;height:142px;border:3px solid var(--white);box-shadow:0 0 4px rgba(0,0,0,.3);background:linear-gradient(160deg,#c9c0b3,#7d8a94 60%,#b9bdc0)}
.why-text{left:210px;top:871px;width:142px;font-size:6.7px;line-height:12.2px;text-align:justify}
.why-text p+p{margin-top:12px}
.video-title{left:376px;top:843px}
.video{left:376px;top:872px;width:251px;height:142px;background:linear-gradient(180deg,#3d3d3d 0 6%,#7a5a45 35%,#a6785a 70%,#6d5140 100%)}
.play{left:110px;top:56px;width:30px;height:30px;border-radius:50%;background:rgba(0,0,0,.55)}
.video .bar{left:0;bottom:0;width:251px;height:10px;background:rgba(0,0,0,.7)}
.footer{left:0;top:1045px;width:705px;height:128px;background:var(--dark);color:#dcdcdc}
.footer h4{font-size:6.8px;font-weight:700;color:var(--white);text-transform:uppercase}
.footer .season{font-size:7.5px;color:var(--white);margin:11px 0 4px}
.footer p{font-size:6.3px;line-height:13.5px}
.col1{left:78px;top:26px}
.col2{left:272px;top:26px}
.col3{left:480px;top:26px}
.col3 p{line-height:11.5px}
.bottom{left:0;top:1173px;width:705px;height:27px;background:var(--darker);color:#e0e0e0;font-size:6.3px}
.bottom .icons{left:78px;top:5px;display:flex;gap:3px}
.bottom .icons span{width:17px;height:17px;border:1px solid #bbb;border-radius:50%}
.bottom .copy{right:80px;top:9px}
</style>
</head>
<body>

<div class="topbar abs">
  <div class="social abs"><span></span><span></span><span></span><span></span><span></span><span></span></div>
  <div class="contact abs"><span>&#9993; Email: hello@fernvitality.example</span><span>&#9742; Phone: 0400 123 456</span></div>
</div>

<header class="header abs">
  <div class="logo abs">FERN Vitality</div>
  <nav class="nav abs">
    <a class="active">Home</a><a>About</a><a>Training</a><a>Gallery</a><a>Testimonials</a><a style="margin-right:0">Contact</a>
  </nav>
</header>

<section class="hero abs" role="img" aria-label="Three women stretching in a bright studio during a group class">
  <svg width="705" height="315" viewBox="0 0 705 315">
    <polygon points="430,0 705,0 705,315 330,315" fill="#abd036" opacity=".55"/>
    <polyline points="16,184 6,198 16,212" fill="none" stroke="#fff" stroke-width="1.5"/>
    <polyline points="684,184 694,198 684,212" fill="none" stroke="#fff" stroke-width="1.5"/>
  </svg>
  <div class="hero-title abs">FERN VITALITY &amp; HEALTH</div>
  <div class="hero-text abs">All my life I have been looking for a place that I can train in a comfortable and natural environment instead been surrounded by concrete walls &amp; floors, what I am offering in my studio gym is a natural organic style of training that clients can feel...</div>
</section>

<div class="about-photo abs" role="img" aria-label="Portrait of the trainer outdoors"></div>
<h2 class="section-title about-title abs">About Fern Fit &amp; Health</h2>
<p class="about-text abs">FERNFIT has trainers that have a Diploma of fitness from the Ridgeway Institute &amp; are trained and qualified with the latest training techniques available anywhere in Australia, to give clients a better &amp; more reliable service with cutting edge training programs and testing. The foundation of this business will be to service clients by functional training techniques and some machines, with a combination of group classes &amp; one on one Personal training. We also have an area for Pilates experience this is a very Japanese influenced setting &amp; is called, Organic Pilates experience.</p>
<div class="btn abs">Read More &#8853;</div>

<div class="rule abs" style="top:573px"></div>

<h2 class="section-title services-title abs">Our Services</h2>
<svg class="arrows abs" width="15" height="10" viewBox="0 0 15 10"><polyline points="5,1 1,5 5,9" fill="none" stroke="#555" stroke-width="1.2"/><polyline points="10,1 14,5 10,9" fill="none" stroke="#555" stroke-width="1.2"/></svg>

<div class="card orange abs" style="left:78px">
  <div class="pic" role="img" aria-label="Coach helping a client use an inhaler outdoors" style="background:linear-gradient(180deg,#a9c4dc,#c07a5e)"></div>
  <h3>Asthma</h3>
  <p>Sed ut perspiciloratis unde omns istenatus lomerror sit voluptatm accu santium doloremque.</p>
  <div class="more">Read More</div>
</div>
<div class="card green abs" style="left:218px">
  <div class="pic" role="img" aria-label="Blood glucose meter on a wooden table" style="background:linear-gradient(180deg,#8a6a4e,#c79a6f)"></div>
  <h3>Diabetes</h3>
  <p>Sed ut perspiciloratis unde omns istenatus lomerror sit voluptatm accu santium doloremque.</p>
  <div class="more">Read More</div>
</div>
<div class="card orange abs" style="left:358px">
  <div class="pic" role="img" aria-label="Person resting on a sofa at home" style="background:linear-gradient(180deg,#8e8a86,#5e6572)"></div>
  <h3>Obesity</h3>
  <p>Sed ut perspiciloratis unde omns istenatus lomerror sit voluptatm accu santium doloremque.</p>
  <div class="more">Read More</div>
</div>
<div class="card green abs" style="left:498px">
  <div class="pic" role="img" aria-label="Athlete training with a medicine ball" style="background:linear-gradient(180deg,#bdbdbd,#8a6f63)"></div>
  <h3>Sports Performance</h3>
  <p>Sed ut perspiciloratis unde omns istenatus lomerror sit voluptatm accu santium doloremque.</p>
  <div class="more">Read More</div>
</div>

<div class="rule abs" style="top:822px"></div>

<h2 class="section-title why-title abs">Why Train With Us</h2>
<div class="why-photo abs" role="img" aria-label="Smiling trainer leaning on an exercise ball"></div>
<div class="why-text abs">
  <p>Our training services covers a wide variety of clients from different walks of life, like builders, plumbers, electricians, mechanics, truck drivers to your everyday common office workers, teachers, taxi drivers, nurses &amp; doctors and more.</p>
  <p>All these people are all eligible for this type of training. It is a great way to restore functional movement to deal with the everyday demands of your body &amp; just general fitness, health &amp; wellbeing.</p>
</div>

<h2 class="section-title video-title abs">Our Video</h2>
<div class="video abs" role="img" aria-label="Video still of the outdoor timber training deck with plants">
  <svg class="play abs" width="30" height="30" viewBox="0 0 30 30"><polygon points="12,9 21,15 12,21" fill="#fff"/></svg>
  <div class="bar abs"></div>
</div>

<footer class="footer abs">
  <div class="col1 abs">
    <h4>Trading Hours</h4>
    <div class="season">April – September</div>
    <p>Monday – Friday 4.00pm - 6.00pm (Finish by 7:00pm )<br>Saturday- 12:00pm – 5-00pm &nbsp;(Finish by 6:00pm)<br>Sunday - 6:00am – 11:00am(Finish by 12:00pm)</p>
  </div>
  <div class="col2 abs">
    <h4>&nbsp;</h4>
    <div class="season">October – March</div>
    <p>Monday – Friday 6:00am – 7:00pm (Finish by 8:00pm)<br>Saturday – 12:00pm – 5-00pm (Finish by 6:00pm)<br>Sunday- 6:00am – 11:00am (Finish by 12:00pm)</p>
  </div>
  <div class="col3 abs">
    <h4>Contact Us</h4>
    <p style="margin-top:11px">The business is located 42 Willow Lane<br>Greenvale 3999 &amp; service the surrounding areas.<br>For enquiries &amp; Bookings</p>
    <p style="margin-top:3px">&#9742; Mobile: 0400123456</p>
    <p style="margin-top:3px">&#9993; Email: hello@fernvitality.example</p>
  </div>
</footer>

<div class="bottom abs">
  <div class="icons abs"><span></span><span></span><span></span><span></span></div>
  <div class="copy abs">© 2016 copyrights are reserved. Fern Vitality</div>
</div>

</body>
</html>
```